New Business Card Design Project

We require a business card design for Vexalund, a newly established Indian company.
Our focus is on the development, manufacturing, and export of a diverse array of pharmaceutical products on a global scale. The card should convey a professional appearance, as our primary markets are in Africa, China, and Southeast Asian nations.
We envision a two-sided business card, with the reverse side dedicated to a logo set against a solid color or an elegantly designed pattern. The corners should be rounded. We would appreciate seeing both horizontal and vertical design options. We trust the designer to utilize their expertise in creating this design.

The content for the business card is included in the attached Word file.

Target Market(s)

Our primary markets are in Africa, China, and Southeast Asian, Latin America, Maldives, Sri Lanka

Industry/Entity Type

Pharmaceutical Manufacturing and Export

Contact Information for Business Card

Colors

Designer to choose colors to be used in the design.

Requirements
Must have
• The reverse side of the business card features solely the logo along with the tagline, "Care Beyond Borders."
Should not have
• The logo should not exceed two instances, encompassing both the front and back sides of the card.

```html
<!DOCTYPE html>
<html lang="en">
<head>
<meta charset="UTF-8">
<title>Vexalund Business Card</title>
<link href="https://fonts.googleapis.com/css2?family=Montserrat:wght@500;600&family=Lato:wght@400&display=swap" rel="stylesheet">
<style>
  :root {
    --backdrop: #2b2c2f;
    --brand-blue: #2ba8e0;
    --brand-coral: #f0604b;
    --ink-grey: #5f6368;
    --paper: #ffffff;
  }
  * { margin: 0; padding: 0; box-sizing: border-box; }
  html, body {
    width: 1200px; height: 952px; overflow: hidden;
    background: var(--backdrop);
  }
  .sheet {
    width: 1200px; height: 952px;
    display: flex; align-items: center; justify-content: center; gap: 40px;
  }
  .card {
    position: relative;
    width: 540px; height: 309px;
    border-radius: 14px;
    overflow: hidden;
    box-shadow: 0 18px 40px rgba(0,0,0,.45);
  }
  /* Front side */
  .card-front { background: var(--paper); }
  .holder {
    position: absolute; left: 34px; top: 34px;
  }
  .holder-name {
    font-family: "Montserrat", sans-serif; font-weight: 600;
    font-size: 22px; letter-spacing: .5px; color: var(--brand-blue);
  }
  .holder-name .surname { color: var(--brand-coral); }
  .holder-role {
    font-family: "Lato", sans-serif; font-size: 15px;
    color: var(--ink-grey); margin-top: 2px;
  }
  .contact-list {
    position: absolute; left: 34px; top: 126px;
    list-style: none;
    font-family: "Lato", sans-serif; font-size: 12px; color: var(--ink-grey);
  }
  .contact-item { display: flex; align-items: flex-start; gap: 8px; margin-bottom: 7px; line-height: 1.3; }
  .contact-icon { flex: none; width: 15px; height: 15px; }
  .brand-decoration {
    position: absolute; right: 0; bottom: 0;
    width: 250px; height: 200px;
    border-top-left-radius: 40px;
    background: linear-gradient(135deg, var(--brand-blue) 0%, var(--brand-blue) 45%, var(--brand-coral) 55%, var(--brand-coral) 100%);
  }
  /* Back side */
  .card-back {
    background: var(--brand-blue);
    display: flex; flex-direction: column; align-items: center; justify-content: center;
    color: var(--paper);
  }
  .wordmark {
    display: flex; align-items: center; gap: 12px;
    font-family: "Montserrat", sans-serif; font-weight: 600;
    font-size: 46px; letter-spacing: 1px;
  }
  .wordmark-dot { width: 16px; height: 16px; border-radius: 50%; background: var(--paper); }
  .tagline {
    display: flex; align-items: center; gap: 10px; margin-top: 6px;
    font-family: "Lato", sans-serif; font-size: 15px; letter-spacing: 1px;
  }
  .tagline-rule { width: 40px; height: 1px; background: var(--paper); }
</style>
</head>
<body>
<main class="sheet">
  <section class="card card-front" aria-label="Business card front">
    <div class="holder">
      <h1 class="holder-name">ROHAN K. <span class="surname">SATHE</span></h1>
      <p class="holder-role">CEO/Vexalund</p>
    </div>
    <ul class="contact-list">
      <li class="contact-item">
        <svg class="contact-icon" viewBox="0 0 16 16"><rect width="16" height="16" rx="3" fill="var(--brand-coral)"/><path d="M8 3.2a3 3 0 0 0-3 3c0 2.2 3 6 3 6s3-3.8 3-6a3 3 0 0 0-3-3z" fill="#fff"/><circle cx="8" cy="6.2" r="1.1" fill="var(--brand-coral)"/></svg>
        <span>14, Neelkamal Colony, Akola,<br>444001, India</span>
      </li>
      <li class="contact-item">
        <svg class="contact-icon" viewBox="0 0 16 16"><rect width="16" height="16" rx="3" fill="var(--brand-blue)"/><path d="M5 3.5l2 2-1.2 1.3a6 6 0 0 0 3.4 3.4L10.5 9l2 2-1.3 1.5C7.5 12.3 3.7 8.5 3.5 4.8z" fill="#fff"/></svg>
        <span>+919800012345</span>
      </li>
      <li class="contact-item">
        <svg class="contact-icon" viewBox="0 0 16 16"><rect width="16" height="16" rx="3" fill="var(--brand-blue)"/><rect x="3.5" y="5" width="9" height="6.5" fill="none" stroke="#fff" stroke-width="1.2"/><path d="M3.5 5l4.5 3.5L12.5 5" fill="none" stroke="#fff" stroke-width="1.2"/></svg>
        <span>rsathe@vexalund.com</span>
      </li>
      <li class="contact-item">
        <svg class="contact-icon" viewBox="0 0 16 16"><rect width="16" height="16" rx="3" fill="var(--brand-blue)"/><path d="M5 3.5l6.5 5-3 .4 1.6 3-1.2.6-1.6-3-2.3 2z" fill="#fff"/></svg>
        <span>rsathe@vexalund.com</span>
      </li>
    </ul>
    <div class="brand-decoration" role="img" aria-label="Large blue and coral brand symbol decoration"></div>
  </section>

  <section class="card card-back" aria-label="Business card back">
    <div class="wordmark"><span class="wordmark-dot"></span>Vexalund</div>
    <p class="tagline"><span class="tagline-rule"></span>Care Beyond Borders<span class="tagline-rule"></span></p>
  </section>
</main>
</body>
</html>
```